Design a product reviews website

We need a website design and simple logo for the brand Venlotix.com. The website will provide reviews of technology products and services. The brand and website should be approachable but should also be trustworthy and high quality. The deliverable should be designs, specs and assets that I can provide to a development team to build the website.

Target Market(s)

People researching products to buy.

Industry/Entity Type

Product

Logo Text

Venlotix.com

Number of Pages Required

5+ page

Font styles to use
Sans Serif

Colors
0492cd
0355a3
3176b5
33a6d7
85cae6
85abd2
cedeed
cee9f5

Requirements
Must have
• - Designs for the Homepage, Category and Article pages.
• - Designs for web and mobile.
• - Designs details for the engineering team to use for development.
• - I'm open to other colors than the preferences I chose but I'm more likely to like blues, greys and blacks.

```html
<!DOCTYPE html>
<html lang="en">
<head>
<meta charset="utf-8">
<title>Venlotix.com – Product Reviews</title>
<link href="https://fonts.googleapis.com/css2?family=Montserrat:wght@400;500;600&family=Raleway:wght@300&display=swap" rel="stylesheet">
<style>
:root{
  --blue:#0492cd;
  --blue-dark:#0355a3;
  --ink:#222;
  --text:#444;
  --muted:#666;
  --page:#f3f3f3;
  --card:#fff;
  --line:#e4e4e4;
  --footer:#2d2f33;
  --tag-light:#eeeeee;
}
*{box-sizing:border-box;margin:0;padding:0}
html,body{width:674px;height:1200px;overflow:hidden}
body{position:relative;background:var(--page);font-family:"Montserrat",Arial,sans-serif;color:var(--text)}

.site-header{position:absolute;left:0;top:0;width:674px;height:44px;background:#fff;border-bottom:2px solid var(--blue)}
.brand{position:absolute;left:56px;top:13px;font-size:16px;font-weight:600;color:var(--ink);letter-spacing:.2px}
.menu-toggle{position:absolute;left:595px;top:16px}

.hero{position:absolute;left:0;top:44px;width:674px;height:245px;
  background:radial-gradient(ellipse 170px 110px at 320px 120px,#6d7680 0%,#3c4148 45%,transparent 75%),linear-gradient(180deg,#2a2623 0%,#1d1a18 60%,#141211 100%)}
.hero-title{position:absolute;left:0;top:64px;width:674px;text-align:center;font-family:"Raleway",Arial,sans-serif;font-weight:300;font-size:21px;line-height:22px;color:#fff}
.search-wrap{position:absolute;left:186px;top:126px;width:280px;height:43px;background:rgba(90,96,104,.45)}
.search-input{position:absolute;left:15px;top:12px;width:210px;height:20px;background:#fff;font-size:7px;color:#999;padding:6px 8px}
.search-btn{position:absolute;left:228px;top:12px;width:32px;height:20px;background:var(--blue);display:flex;align-items:center;justify-content:center}

.panel{position:absolute;background:var(--card)}
.categories{left:56px;top:320px;width:146px;height:192px}
.panel-head{height:24px;background:var(--blue);color:#fff;font-size:9px;font-weight:600;display:flex;align-items:center;padding-left:8px;gap:4px;border-bottom:2px solid var(--blue-dark)}
.cat-list{list-style:none;padding:2px 8px 0 8px}
.cat-list li{height:23.6px;border-bottom:1px solid var(--line);font-size:6.5px;color:var(--text);display:flex;align-items:center;gap:5px}
.cat-list li:last-child{border-bottom:none}
.cat-list li::before{content:"»";font-size:7px;color:#888}

.card{position:absolute;background:var(--card);padding:5px}
.thumb{position:relative;width:100%}
.tags{position:absolute;right:0;bottom:0;display:flex;font-size:6px;font-weight:600}
.tag{height:12px;display:flex;align-items:center;padding:0 8px}
.tag-home{background:var(--tag-light);color:#222}
.tag-cat{background:var(--blue);color:#fff}
.tags.solo .tag-home{background:var(--blue);color:#fff}
.card-title{font-size:8.6px;font-weight:500;color:var(--ink);margin:10px 1px 0}
.meta{display:flex;align-items:center;font-size:6.6px;color:var(--muted);margin:8px 1px 0}
.avatar{width:12px;height:12px;border-radius:50%;background:#cfe3dc;border:1px solid #b8cfc7;margin-right:8px}
.meta .date{margin-left:auto;margin-right:30px}

.popular-head{height:24px;background:var(--blue);color:#fff;font-size:9px;font-weight:600;display:flex;align-items:center;padding-left:9px}

.tabs{position:absolute;left:234px;top:318px;width:387px;height:25px;border-bottom:1px solid var(--line)}
.tab{position:absolute;top:0;height:25px;font-size:7.2px;font-weight:500;display:flex;align-items:center;letter-spacing:.3px}
.tab-active{left:0;width:119px;justify-content:center;color:var(--blue);background:#fff;border-top:2px solid var(--blue);border-left:1px solid var(--line);border-right:1px solid var(--line)}
.tab-plain{left:133px;color:#333}

.load-more{position:absolute;left:294px;top:1120px;width:87px;height:22px;background:var(--blue);color:#fff;font-size:7px;font-weight:600;display:flex;align-items:center;justify-content:center;gap:5px;border-bottom:2px solid var(--blue-dark)}

.site-footer{position:absolute;left:0;top:1171px;width:674px;height:29px;background:var(--footer);color:#ccc;font-size:7px;display:flex;align-items:center;justify-content:center}
.site-footer strong{color:#fff;font-weight:600;margin:0 2px}
</style>
</head>
<body>

<header class="site-header">
  <div class="brand">Venlotix.com</div>
  <svg class="menu-toggle" width="13" height="11" viewBox="0 0 13 11" aria-label="Menu">
    <g fill="#2a3a4a">
      <rect x="0" y="0" width="3" height="3"/><rect x="4" y="0" width="9" height="3"/>
      <rect x="0" y="4" width="3" height="3"/><rect x="4" y="4" width="9" height="3"/>
      <rect x="0" y="8" width="3" height="3"/><rect x="4" y="8" width="9" height="3"/>
    </g>
  </svg>
</header>

<section class="hero" role="img" aria-label="Photo of a grey portable speaker on a dark wooden table">
  <h1 class="hero-title">The Best Product And Services Reviews<br>And Rankings</h1>
  <div class="search-wrap">
    <div class="search-input">Search</div>
    <div class="search-btn">
      <svg width="10" height="10" viewBox="0 0 10 10"><circle cx="4" cy="4" r="3" fill="none" stroke="#fff" stroke-width="1.6"/><line x1="6.2" y1="6.2" x2="9" y2="9" stroke="#fff" stroke-width="1.8"/></svg>
    </div>
  </div>
</section>

<aside class="panel categories">
  <div class="panel-head">
    <svg width="8" height="7" viewBox="0 0 8 7"><g fill="#fff"><rect y="0" width="8" height="1.4"/><rect y="2.8" width="8" height="1.4"/><rect y="5.6" width="8" height="1.4"/></g></svg>
    CATEGORIES
  </div>
  <ul class="cat-list">
    <li>APPLIANCES</li><li>COMPUTERS</li><li>ELECTRONIC</li><li>HOME SECURITY</li><li>MOBILE</li><li>SMART HOME</li><li>SOFTWARE</li>
  </ul>
</aside>

<article class="card" style="left:56px;top:526px;width:146px;height:232px">
  <div class="popular-head">POPULAR</div>
  <div class="thumb" style="height:153px;background:linear-gradient(160deg,#7c6a58,#3a3330 55%,#6b5240)" role="img" aria-label="Photo of a video camera with a microphone on a desk"></div>
  <h3 class="card-title">Dolore Magna Aliquam</h3>
  <div class="meta"><span class="avatar"></span>John Smith<span class="date">Aug 11, 2016</span></div>
</article>

<article class="card" style="left:56px;top:770px;width:146px;height:155px">
  <div class="thumb" style="height:99px;background:linear-gradient(180deg,#e8e8e8 0%,#2a2a2a 10%,#1c1c1c 100%)" role="img" aria-label="Photo of a black wireless speaker">
    <div class="tags solo"><span class="tag tag-home">HOME</span></div>
  </div>
  <h3 class="card-title">Dolore Magna Aliquam</h3>
  <div class="meta"><span class="avatar"></span>John Smith<span class="date">Aug 11, 2016</span></div>
</article>

<article class="card" style="left:56px;top:936px;width:146px;height:154px">
  <div class="thumb" style="height:98px;background:linear-gradient(180deg,#7a4a2a 0%,#b89070 45%,#e8e4e4 70%,#c9a27a 100%)" role="img" aria-label="Photo of a white baby monitor device on a table">
    <div class="tags solo"><span class="tag tag-home">HOME</span></div>
  </div>
  <h3 class="card-title">Dolore Magna Aliquam</h3>
  <div class="meta"><span class="avatar"></span>John Smith<span class="date">Aug 11, 2016</span></div>
</article>

<nav class="tabs">
  <div class="tab tab-active">LATEST&nbsp; COMPARISONS</div>
  <div class="tab tab-plain">PPRODUCT ARTICLE</div>
</nav>

<article class="card" style="left:233px;top:357px;width:180px;height:194px">
  <div class="thumb" style="height:130px;background:linear-gradient(90deg,#5a6068 0%,#262626 20%,#1a1a1a 70%,#6a7078 100%)" role="img" aria-label="Photo of a black cylindrical smart speaker">
    <div class="tags"><span class="tag tag-home">HOME</span><span class="tag tag-cat">SPEAKERS</span></div>
  </div>
  <h3 class="card-title">Ipsum Dolor Sitamet</h3>
  <div class="meta"><span class="avatar"></span>John Smith<span class="date">Aug 11, 2016</span></div>
</article>

<article class="card" style="left:233px;top:563px;width:180px;height:234px">
  <div class="thumb" style="height:177px;background:linear-gradient(180deg,#e6e2dc 0%,#c8b8a4 35%,#5fbcbc 60%,#d8d6d2 100%)" role="img" aria-label="Photo of a teal portable speaker on an office desk">
    <div class="tags"><span class="tag tag-home">HOME</span><span class="tag tag-cat">SPEAKERS</span></div>
  </div>
  <h3 class="card-title">Dolore Magna Aliquam Eravolutpat</h3>
  <div class="meta"><span class="avatar"></span>John Smith<span class="date">Aug 11, 2016</span></div>
</article>

<article class="card" style="left:233px;top:808px;width:180px;height:282px">
  <div class="thumb" style="height:225px;background:linear-gradient(180deg,#e4e6e8 0%,#c9ccd0 35%,#2f5f9a 50%,#d6d4d0 65%,#eeeeee 100%)" role="img" aria-label="Photo of a modern kitchen with island and stools">
    <div class="tags solo"><span class="tag tag-home">HOME</span></div>
  </div>
  <h3 class="card-title">Dolore Magna Aliq Eravolutpat</h3>
  <div class="meta"><span class="avatar"></span>John Smith<span class="date">Aug 11, 2016</span></div>
</article>

<article class="card" style="left:430px;top:357px;width:180px;height:156px">
  <div class="thumb" style="height:99px;background:linear-gradient(180deg,#5a5654 0%,#2a2a2a 40%,#1a1a1a 70%,#dcd8d4 100%)" role="img" aria-label="Photo of a black square smart hub in a kitchen">
    <div class="tags"><span class="tag tag-home">HOME</span><span class="tag tag-cat">SPEAKERS</span></div>
  </div>
  <h3 class="card-title">Ipsum Dolor Sitamet</h3>
  <div class="meta"><span class="avatar"></span>John Smith<span class="date">Aug 11, 2016</span></div>
</article>

<article class="card" style="left:430px;top:526px;width:180px;height:156px">
  <div class="thumb" style="height:100px;background:linear-gradient(90deg,#5a6068 0%,#262626 20%,#1a1a1a 70%,#6a7078 100%)" role="img" aria-label="Photo of a black cylindrical smart speaker">
    <div class="tags"><span class="tag tag-home">HOME</span><span class="tag tag-cat">SPEAKERS</span></div>
  </div>
  <h3 class="card-title">Ipsum Dolor Sitamet</h3>
  <div class="meta"><span class="avatar"></span>John Smith<span class="date">Aug 11, 2016</span></div>
</article>

<article class="card" style="left:431px;top:692px;width:180px;height:155px">
  <div class="thumb" style="height:99px;background:linear-gradient(90deg,#5a6068 0%,#262626 20%,#1a1a1a 70%,#6a7078 100%)" role="img" aria-label="Photo of a black cylindrical smart speaker">
    <div class="tags"><span class="tag tag-home">HOME</span><span class="tag tag-cat">SPEAKERS</span></div>
  </div>
  <h3 class="card-title">Ipsum Dolor Sitamet</h3>
  <div class="meta"><span class="avatar"></span>John Smith<span class="date">Aug 11, 2016</span></div>
</article>

<article class="card" style="left:432px;top:858px;width:181px;height:233px">
  <div class="thumb" style="height:177px;background:linear-gradient(180deg,#e6e2dc 0%,#c8b8a4 35%,#5fbcbc 60%,#d8d6d2 100%)" role="img" aria-label="Photo of a teal portable speaker on an office desk">
    <div class="tags"><span class="tag tag-home">HOME</span><span class="tag tag-cat">SPEAKERS</span></div>
  </div>
  <h3 class="card-title">Dolore Magna Aliquam Eravolutpat</h3>
  <div class="meta"><span class="avatar"></span>John Smith<span class="date">Aug 11, 2016</span></div>
</article>

<div class="load-more">
  <svg width="10" height="10" viewBox="0 0 10 10"><g fill="#fff"><circle cx="5" cy="1.2" r="1"/><circle cx="8.8" cy="5" r="1"/><circle cx="5" cy="8.8" r="1"/><circle cx="1.2" cy="5" r="1"/><circle cx="7.7" cy="2.3" r=".8"/><circle cx="7.7" cy="7.7" r=".8"/><circle cx="2.3" cy="7.7" r=".8"/><circle cx="2.3" cy="2.3" r=".8"/></g></svg>
  LOAD MORE
</div>

<footer class="site-footer">Copyright © 2016 <strong>NORVALE</strong>| &nbsp;All Rights Reserved.</footer>

</body>
</html>
```